Modern looking signage for dental office.

Exterior signage for passing cars
Updates
Need extra days to review
Target Market(s)
Cars passing by
Font styles to use
Sans Serif
Colors
3276b5
Requirements
Must have
- Logo
- OPEN ON SUTURDAY AND SUNDAY
- NIGHT CLINIC AVAILABLE
- PLEASE USE THE FONT TYPE IN FILE 4 UPLOADED BELOW.
- (847) 302-7469
- Modern looking

```html
<!DOCTYPE html>
<html lang="en">
<head>
<meta charset="utf-8">
<title>Peakline Dental – Exterior Sign</title>
<link rel="stylesheet" href="https://fonts.googleapis.com/css2?family=Exo+2:wght@300;600;700&family=Encode+Sans+Condensed:wght@400&display=swap">
<style>
  :root {
    --sign-white: #ffffff;
    --backdrop: #eef0f2;
    --brand-blue: #0a5299;
    --ink-dark: #3b3936;
    --stripe-dark: #4a4846;
    --phone-ink: #1c1c1c;
  }
  * { margin: 0; padding: 0; box-sizing: border-box; }
  html, body {
    width: 1200px;
    height: 1200px;
    overflow: hidden;
    background: var(--backdrop);
  }
  .sign {
    position: absolute;
    left: 40px;
    top: 250px;
    width: 1120px;
    height: 700px;
    background: var(--sign-white);
    box-shadow: 0 6px 24px rgba(0,0,0,0.12);
    overflow: hidden;
  }
  .sign__stripe {
    position: absolute;
    top: 0;
    bottom: 0;
    right: 30px;
    width: 72px;
    background: var(--stripe-dark);
  }
  .brand {
    position: absolute;
    left: 80px;
    top: 95px;
    width: 900px;
    display: flex;
    align-items: center;
    gap: 26px;
  }
  .brand__dot {
    width: 140px;
    height: 140px;
    border: 2px solid var(--ink-dark);
    border-radius: 50%;
    flex: none;
  }
  .brand__words {
    display: flex;
    flex-direction: column;
    align-items: center;
    gap: 14px;
  }
  .brand__name {
    font-family: "Exo 2", sans-serif;
    font-weight: 300;
    font-size: 86px;
    line-height: 1;
    letter-spacing: 1px;
    color: var(--ink-dark);
    white-space: nowrap;
  }
  .brand__tagline {
    font-family: "Encode Sans Condensed", sans-serif;
    font-weight: 400;
    font-size: 40px;
    line-height: 1;
    letter-spacing: 1px;
    color: var(--ink-dark);
    white-space: nowrap;
  }
  .night-band {
    position: absolute;
    left: 0;
    right: 0;
    top: 385px;
    height: 120px;
    background: var(--brand-blue);
    display: flex;
    align-items: center;
    padding-left: 64px;
  }
  .night-band__text {
    font-family: "Exo 2", sans-serif;
    font-weight: 700;
    font-size: 76px;
    letter-spacing: 1px;
    color: var(--sign-white);
    white-space: nowrap;
  }
  .contact-phone {
    position: absolute;
    left: 40px;
    top: 560px;
    font-family: "Exo 2", sans-serif;
    font-weight: 700;
    font-size: 64px;
    color: var(--phone-ink);
    white-space: nowrap;
  }
  .weekend-hours {
    position: absolute;
    left: 560px;
    width: 420px;
    top: 562px;
    text-align: center;
    font-family: "Exo 2", sans-serif;
    font-weight: 600;
    font-size: 32px;
    line-height: 1.15;
    letter-spacing: 1px;
    color: var(--brand-blue);
  }
</style>
</head>
<body>
  <main class="sign">
    <div class="sign__stripe"></div>

    <div class="brand">
      <span class="brand__dot"></span>
      <div class="brand__words">
        <span class="brand__name">PEAKLINE DENTAL</span>
        <span class="brand__tagline">MODERN GENERAL DENTISTRY</span>
      </div>
    </div>

    <div class="night-band">
      <p class="night-band__text">Night Clinic Available</p>
    </div>

    <p class="contact-phone">(847) 302-7469</p>
    <p class="weekend-hours">Open on<br>Saturday and Sunday</p>
  </main>
</body>
</html>
```